Web Design Project

We need a web design for a new company. We have a logo, and we've identified the style of a website that we'd like to adapt (www.brindlemoor.com). We do not sell to the public. The purpose of the site is (1) to allow our appointed sales partners to log in to our proprietary database system and (2) to provide a basic web presence and some basic information about our company.

We sell business insurance through independent agents - our sales partners.

Please do not use a photo of a person/s as a central design element, or at all.

Target Market(s)

The purpose of the site is not to sell, but to provide a professional landing page for a log in and some basic company information.

Industry/Entity Type

Business

Requirements
Must have
• A professional look. Agent log in must be central, clear and easy. Use of our logo and our colors.
Should not have
• Photos of people

```html
<!DOCTYPE html>
<html lang="en">
<head>
<meta charset="utf-8">
<title>Harlow Creek Insurance</title>
<link rel="stylesheet" href="https://fonts.googleapis.com/css2?family=Source+Sans+3:wght@400;600&display=swap">
<style>
:root{
  --navy:#0d4466;
  --navy-deep:#083451;
  --panel:#062c45;
  --green:#5fb317;
  --green-text:#78c21e;
  --blue-head:#1f6fa3;
  --grey-text:#6b6b6b;
  --body-text:#4a4a4a;
  --line:#c9c9c9;
  --red-link:#a3191f;
  --white:#ffffff;
}
*{box-sizing:border-box;margin:0;padding:0}
html,body{width:887px;height:1200px;overflow:hidden}
body{font-family:"Source Sans 3",Arial,sans-serif;background:var(--white);position:relative;color:var(--body-text)}
.abs{position:absolute}
.top-band{left:0;top:0;width:887px;height:419px;background:linear-gradient(180deg,var(--navy) 0,var(--navy) 128px,#0a3a5a 130px,#0f4a70 300px,#0b3d5d 419px)}
.header-rule{left:0;top:128px;width:887px;height:2px;background:#0a2f48}
.brand-mark{left:26px;top:22px;width:80px;height:80px;background:#1a5a85;border:3px solid #c7d0d8;border-radius:6px}
.brand-name{left:122px;top:42px;font-size:23px;color:var(--white);letter-spacing:.5px;font-weight:400}
.search{left:705px;top:39px;width:154px;height:20px;background:var(--white);border:1px solid #9bb;border-radius:3px;font-size:10px;font-style:italic;color:#5a7a9a;padding:3px 7px}
.search svg{position:absolute;right:5px;top:3px}
.nav{left:242px;top:92px;width:625px;height:34px;background:#082f49;display:flex;border-radius:2px 2px 0 0}
.nav a{color:var(--white);text-decoration:none;font-size:11.5px;display:flex;align-items:center;justify-content:center;border-right:1px solid #0f4466;height:100%;white-space:nowrap}
.nav a.on{background:var(--green)}
.slider-shadow{left:53px;top:440px;width:800px;height:46px;background:linear-gradient(180deg,#dfe3e6,rgba(255,255,255,0))}
.slider{left:42px;top:163px;width:810px;height:300px}
.slide-photo{left:56px;top:180px;width:484px;height:260px;border:3px solid var(--white);background:linear-gradient(135deg,#7d93b8 0%,#a9bbd6 45%,#6b7fa6 100%)}
.slide-title{left:594px;top:214px;font-size:21px;color:var(--green-text)}
.slide-text{left:597px;top:260px;width:230px;font-size:10px;line-height:21px;color:#e4eef5}
.btn{background:linear-gradient(180deg,#74c42a,#4e9f10);color:var(--white);border-radius:3px;display:flex;align-items:center;justify-content:center}
.learn{left:695px;top:357px;width:119px;height:28px;font-size:11.5px;box-shadow:2px 3px 4px rgba(0,0,0,.35)}
.dots{left:784px;top:430px;display:flex;gap:4px}
.dots i{width:8px;height:8px;border-radius:50%;background:var(--white)}
.dots i.on{background:var(--green)}
.signin{left:55px;top:502px;width:795px;height:85px;background:var(--panel);border-radius:3px}
.signin-label{left:74px;top:532px;font-size:15px;color:var(--green-text)}
.field{top:531px;width:177px;height:24px;background:var(--white);border:1px solid #cfd6db;border-radius:4px;font-size:9.5px;color:#888;padding:5px 12px}
.signin-btn{left:561px;top:531px;width:77px;height:22px;font-size:11.5px;border-radius:1px}
.forgot{left:656px;top:535px;font-size:10px;color:var(--white)}
.register{left:761px;top:535px;font-size:10px;color:var(--white);text-decoration:underline}
.welcome{left:55px;top:615px;font-size:18px;color:var(--grey-text);font-weight:400}
.welcome span{color:var(--blue-head)}
.dotted{left:57px;top:647px;width:476px;border-top:1px dotted #777}
.about{left:53px;top:660px;width:530px;font-size:10px;line-height:18.2px;color:#555}
.about p+p{margin-top:18px}
.more{font-size:9.5px;color:var(--red-link)}
.more-about{left:522px;top:787px}
.about-photo{left:611px;top:650px;width:231px;height:146px;border:1px solid #aaa;background:linear-gradient(135deg,#c8d2cf,#9fb35e 55%,#5e7d1c)}
.divider-glow{left:210px;top:826px;width:470px;height:14px;background:radial-gradient(ellipse at center top,rgba(0,0,0,.08),rgba(0,0,0,0) 70%)}
.col-head{font-size:15px;color:var(--blue-head);font-weight:400}
.news-icon{left:50px;top:858px;width:35px;height:26px;background:#e6e6e6;border:1px solid #bbb}
.news-head{left:93px;top:864px}
.news-rule{left:49px;top:887px;width:218px;border-top:1px solid var(--line)}
.news{left:48px;width:224px;font-size:9.6px;line-height:15.6px;color:#777}
.news b{display:block;font-weight:400;color:#555;font-size:10px;margin-bottom:1px}
.view{left:227px;top:1093px}
.works-head{left:337px;top:864px}
.works-rule{left:337px;top:887px;width:513px;border-top:1px solid var(--line)}
.work-img{left:338px;width:154px;height:83px;border:1px solid #bbb}
.work-text{left:508px;width:340px;font-size:9.6px;line-height:17.3px;color:#888;text-align:justify}
.work-more{left:512px;font-size:10px;color:var(--blue-head)}
.footer{left:0;top:1124px;width:887px;height:76px;background:var(--navy)}
.social{left:32px;top:1149px;display:flex;gap:6px}
.social i{width:17px;height:17px;border-radius:3px;background:#4a86c6}
.social i:nth-child(3){background:#e07b20}
.foot-links{right:25px;top:1138px;font-size:10px;color:var(--white);word-spacing:1px}
.foot-links span{margin:0 8px}
.copyright{right:25px;top:1160px;font-size:10px;color:var(--white)}
</style>
</head>
<body>
<div class="abs top-band"></div>
<div class="abs header-rule"></div>

<div class="abs brand-mark"></div>
<div class="abs brand-name">HARLOW CREEK INSURANCE</div>
<div class="abs search">Search
  <svg width="16" height="14" viewBox="0 0 16 14"><circle cx="6" cy="6" r="4.2" fill="none" stroke="#333" stroke-width="1.8"/><line x1="9" y1="9" x2="14" y2="13" stroke="#333" stroke-width="2.2"/></svg>
</div>

<nav class="abs nav">
  <a class="on" style="width:65px">HOME</a>
  <a style="width:91px">ABOUT US</a>
  <a style="width:163px">HARLOW CREEK INSURANCE</a>
  <a style="width:94px">INVESTORS</a>
  <a style="width:58px">FAQS</a>
  <a style="width:62px">BLOG</a>
  <a style="width:92px;border-right:0">CONTACT US</a>
</nav>

<div class="abs slider-shadow"></div>
<svg class="abs slider" viewBox="0 0 810 300" preserveAspectRatio="none">
  <polygon points="0,0 565,0 565,-2 810,-2 810,300 625,293 12,300 12,278 0,278" fill="#062c45"/>
</svg>
<div class="abs slide-photo" role="img" aria-label="Cupped hands holding soil with a young green seedling"></div>
<div class="abs slide-title">HARLOW CREEK INSURANCE</div>
<div class="abs slide-text">Nunc varius facilisis eros. Sed erat. In in velit quis arcu ornare laoreet. Curabitur adipiscing luctus massa.Integer ut purus ac augue</div>
<div class="abs btn learn">LEARN MORE</div>
<div class="abs dots"><i class="on"></i><i></i><i></i></div>

<section class="abs signin"></section>
<div class="abs signin-label">SIGN IN</div>
<div class="abs field" style="left:160px">User Name</div>
<div class="abs field" style="left:360px">Password</div>
<div class="abs btn signin-btn">SIGN IN</div>
<div class="abs forgot">Forgot password?</div>
<div class="abs register">Register now</div>

<h1 class="abs welcome"><span>Welcome to</span> HARLOW CREEK INSURANCE</h1>
<div class="abs dotted"></div>
<div class="abs about">
  <p>Nunc varius facilisis eros. Sed erat. In in velit quis arcu ornare laoreet. Nunc varius facilisis eros. Sed erat. In in velit quis arcu ornare laoreet. Nunc varius facilisis eros. Sed erat. In in velit quis arcu ornare laoreet. Nunc varius facilisis eros. Sed erat. In in velit quis arcu ornare laoreet. Nunc varius facilisis eros. Sed erat. In in velit quis arcu ornare laoreet. Nunc varius facilisis eros.</p>
  <p>In in velit quis arcu ornare laoreet. Nunc varius facilisis eros. Sed erat. In in velit quis arcu ornare laoreet. Nunc varius facilisis eros. Sed erat. In in velit quis arcu ornare laoreet. Nunc varius facilisis eros. Sed erat. In in velit quis</p>
</div>
<div class="abs more more-about">View More &nbsp;&gt;&gt;</div>
<div class="abs about-photo" role="img" aria-label="Financial charts, a calculator and a pen on a desk"></div>
<div class="abs divider-glow"></div>

<div class="abs news-icon"></div>
<h2 class="abs col-head news-head">Latest News</h2>
<div class="abs news-rule"></div>
<div class="abs news" style="top:906px"><b>Nov 28, 12</b>Sed ut perspiciatis unde omnis iste natus error sit voluptatem accusantium doloremque laudantium, totam rem aperiam, eaque ipsa quae ab illo inventore veritatis et quasi architectoSed ut</div>
<div class="abs news" style="top:996px"><b>Nov 28, 12</b>Sed ut perspiciatis unde omnis iste natus error sit voluptatem accusantium doloremque laudantium, totam rem aperiam, eaque ipsa quae ab illo inventore veritatis et quasi architectoSed ut</div>
<div class="abs more view">VIEW &nbsp;&gt;&gt;</div>

<h2 class="abs col-head works-head">OUR WORKS</h2>
<div class="abs works-rule"></div>
<div class="abs work-img" style="top:904px;background:linear-gradient(135deg,#f1f4f6,#b9c9d4)" role="img" aria-label="A hand watering a plant shaped like a dollar sign"></div>
<div class="abs work-text" style="top:906px">Sed ut perspiciatis unde omnis iste natus error sit voluptatem accusantium doloremque laudantium, totam rem aperiam, eaque ipsa quae ab illo inventore veritatis et quasi architecto beatae vitae dicta sunt explicabo.</div>
<div class="abs work-more" style="top:967px">VIEW MORE &gt;&gt;</div>
<div class="abs work-img" style="top:1009px;background:linear-gradient(135deg,#f7f3ee 0%,#e9e3dc 50%,#d9ded2 100%)" role="img" aria-label="Rising red and green growth arrow illustration"></div>
<div class="abs work-text" style="top:1009px">Sed ut perspiciatis unde omnis iste natus error sit voluptatem accusantium doloremque laudantium, totam rem aperiam, eaque ipsa quae ab illo inventore veritatis et quasi architecto beatae vitae dicta sunt explicabo.</div>
<div class="abs work-more" style="top:1072px">VIEW MORE &gt;&gt;</div>

<footer class="abs footer"></footer>
<div class="abs social"><i></i><i></i><i></i><i></i></div>
<div class="abs foot-links">Privacy Policy<span>|</span>Terms of Use<span>|</span>Disclaimer</div>
<div class="abs copyright">© 2012 &nbsp;Harlowcreekinsurance, All Rights Reserved</div>
</body>
</html>
```